Business Card Design Project

Business Card
We are rebranding with a new logo
Industry/Entity Type
Business
Contact Information for Business Card
Dennis Morvale +61 487215963 dennis@quorv.com.au P.O. Box 872 Fernlow QLD 4309
Requirements
Must have
- Logo

```html
<!DOCTYPE html>
<html lang="en">
<head>
<meta charset="utf-8">
<title>Quorv International – Business Card</title>
<link rel="stylesheet" href="https://fonts.googleapis.com/css2?family=Lato:wght@300;400;700;900&display=swap">
<style>
  :root {
    --stage: #3a3a3c;
    --card-white: #ffffff;
    --blue-light: #2aa9e2;
    --blue-mid: #1b8fc8;
    --blue-deep: #0b6e9e;
    --brand-blue: #157fb9;
    --accent-orange: #f4901e;
    --text-light: #ffffff;
  }
  * { margin: 0; padding: 0; box-sizing: border-box; }
  html, body {
    width: 1200px;
    height: 926px;
    overflow: hidden;
    background: var(--stage);
    font-family: "Lato", Arial, sans-serif;
  }
  .canvas {
    position: relative;
    width: 1200px;
    height: 926px;
    display: flex;
    align-items: center;
    justify-content: center;
  }
  .business-card {
    position: relative;
    width: 1000px;
    height: 572px;
    background: var(--card-white);
    overflow: hidden;
    box-shadow: 0 18px 40px rgba(0,0,0,0.35);
  }
  .card-shapes {
    position: absolute;
    inset: 0;
    width: 100%;
    height: 100%;
  }
  .brand {
    position: absolute;
    left: 70px;
    top: 62px;
    color: var(--brand-blue);
    font-weight: 700;
    line-height: 1;
  }
  .brand-name {
    display: block;
    font-size: 64px;
    letter-spacing: 2px;
  }
  .brand-tagline {
    display: block;
    margin-top: 8px;
    font-size: 21px;
    letter-spacing: 4.2px;
  }
  .holder-name {
    position: absolute;
    right: 62px;
    top: 118px;
    color: var(--text-light);
    font-size: 31px;
    font-weight: 300;
    letter-spacing: 1px;
    text-transform: uppercase;
  }
  .holder-name strong { font-weight: 700; }
  .contact-list {
    position: absolute;
    right: 62px;
    bottom: 52px;
    list-style: none;
  }
  .contact-item {
    display: flex;
    align-items: center;
    justify-content: flex-end;
    gap: 14px;
    color: var(--text-light);
    font-size: 25px;
    font-weight: 400;
    letter-spacing: 0.6px;
    height: 38px;
  }
  .contact-icon {
    width: 30px;
    height: 30px;
    background: var(--card-white);
    box-shadow: 3px 3px 0 var(--accent-orange);
    display: flex;
    align-items: center;
    justify-content: center;
  }
  .contact-icon svg { width: 20px; height: 20px; fill: var(--blue-mid); }
</style>
</head>
<body>
<main class="canvas">
  <article class="business-card">
    <svg class="card-shapes" viewBox="0 0 1000 572" preserveAspectRatio="none" aria-hidden="true">
      <defs>
        <linearGradient id="blueField" x1="0" y1="0" x2="0" y2="1">
          <stop offset="0" stop-color="var(--blue-light)"/>
          <stop offset="0.55" stop-color="var(--blue-mid)"/>
          <stop offset="1" stop-color="var(--blue-deep)"/>
        </linearGradient>
      </defs>
      <path class="accent-swoosh" fill="var(--accent-orange)"
            d="M0 452 C 170 456, 350 430, 500 352 C 360 448, 180 484, 0 498 Z"/>
      <path class="blue-field" fill="url(#blueField)"
            d="M0 512 C 260 490, 520 330, 640 0 L1000 0 L1000 572 L0 572 Z"/>
    </svg>

    <div class="brand">
      <span class="brand-name">QUORV</span>
      <span class="brand-tagline">INTERNATIONAL</span>
    </div>

    <h1 class="holder-name">Dennis <strong>Morvale</strong></h1>

    <ul class="contact-list">
      <li class="contact-item">
        <span>+61 487215963</span>
        <span class="contact-icon">
          <svg viewBox="0 0 24 24"><path d="M6.6 10.8a15.1 15.1 0 0 0 6.6 6.6l2.2-2.2a1 1 0 0 1 1-.25 11.4 11.4 0 0 0 3.6.57 1 1 0 0 1 1 1V20a1 1 0 0 1-1 1A17 17 0 0 1 3 4a1 1 0 0 1 1-1h3.5a1 1 0 0 1 1 1c0 1.25.2 2.46.57 3.6a1 1 0 0 1-.25 1z"/></svg>
        </span>
      </li>
      <li class="contact-item">
        <span>dennis@quorv.com.au</span>
        <span class="contact-icon">
          <svg viewBox="0 0 24 24"><path d="M3 5h18a1 1 0 0 1 1 1v12a1 1 0 0 1-1 1H3a1 1 0 0 1-1-1V6a1 1 0 0 1 1-1zm1 2.2V17h16V7.2l-8 5.3zM5.5 7 12 11.3 18.5 7z"/></svg>
        </span>
      </li>
      <li class="contact-item">
        <span>P.O. Box 872 Fernlow QLD 4309</span>
        <span class="contact-icon">
          <svg viewBox="0 0 24 24"><path d="M12 2a7 7 0 0 0-7 7c0 5.2 7 13 7 13s7-7.8 7-13a7 7 0 0 0-7-7zm0 9.5A2.5 2.5 0 1 1 12 6.5a2.5 2.5 0 0 1 0 5z"/></svg>
        </span>
      </li>
    </ul>
  </article>
</main>
</body>
</html>
```